Website for my photography business

I need a website for my photography business, Bram Kellet Photography. I need a website that has a landing page with a cover photo of each kind of photography I do. For example, Nature, Weddings, Portraits and Architecture. I want it so that when someone comes onto my website they have to choose which kind of photography page they want to visit. So if they click on the wedding photo it will open to a page with my wedding portfolio images and a contact me button. If they choose nature photography I want them to be redirected to an e-commerce section where they can purchase prints. Architecture and Portraits should open up to their respective portfolios with about me and contact info. I like this kind of format because I want people who come to my website for a specific type of photography to be able to be directed there easily without having to look at a mix of other kinds of photography. I will provide a few files to use as placeholders. I have already purchased the bramkelletphotography.example domain name. A Wix website would be great because I am most familiar with it but I am open to anything.

Industry/Entity Type

Photographer

Number of Pages Required

5+ page

Requirements
Must have
• Landing Page and e-commerce

```html
<!DOCTYPE html>
<html lang="en">
<head>
<meta charset="utf-8">
<title>Bram Kellet Photography – Website Pages</title>
<link href="https://fonts.googleapis.com/css2?family=Poppins:wght@400;500;600;700&family=Great+Vibes&display=swap" rel="stylesheet">
<style>
:root{
  --stage:#e3e3e3;
  --white:#ffffff;
  --topbar:#f4f4f4;
  --ink:#2f2a4a;
  --muted:#6b6b6b;
  --purple:#3d3468;
  --footer:#3f3571;
  --teal:#1d4f6c;
  --teal-active:#2b6077;
  --overlay:rgba(70,58,118,0.45);
  --rule:rgba(255,255,255,0.18);
}
*{box-sizing:border-box;margin:0;padding:0}
html,body{width:1200px;height:1075px;overflow:hidden;background:var(--stage);font-family:"Poppins",sans-serif;color:var(--ink)}
.stage{position:relative;width:1200px;height:1075px}
.page{position:absolute;width:480px;background:var(--white);box-shadow:0 1px 4px rgba(0,0,0,0.12);overflow:hidden}
.page--home{left:89px;top:68px;height:823px}
.page--weddings{left:631px;top:68px;height:940px}
.abs{position:absolute}

.topbar{left:0;top:0;width:480px;height:13px;background:var(--topbar);border-bottom:1px solid #e6e6e6;font-size:5px;color:var(--muted);text-align:center;line-height:13px}
.header{left:0;top:13px;width:480px;height:40px}
.brand{left:44px;top:14px;font-size:9.5px;font-weight:500;color:var(--purple)}
.brand-dot{display:inline-block;width:6px;height:6px;border-radius:50%;background:#e7b93a;margin-right:4px;vertical-align:1px}
.social{top:14px;left:268px;display:flex;gap:2.5px}
.social span{width:14px;height:14px;border-radius:50%;border:1px solid #333;display:block}
.call{left:349px;top:12px;width:87px;height:18px;border-radius:9px;background:var(--teal);color:#fff;font-size:6.3px;font-weight:700;text-align:center;line-height:18px}

.nav{left:0;top:53px;width:480px;height:16px;background:var(--purple);display:flex;padding-left:50px}
.nav a{display:block;padding:0 6.6px;font-size:5.8px;color:#fff;text-decoration:none;line-height:16px;font-weight:500}
.nav a.is-active{background:var(--teal-active)}

.photo{position:absolute;inset:0}
.hero{left:0;top:69px;width:480px}
.hero-panel{position:absolute;left:138px;width:204px;background:var(--overlay);text-align:center;color:#fff}
.hero-title{font-family:"Great Vibes",cursive;font-size:21px;line-height:1;font-weight:400}
.hero-text{font-size:6.8px;font-weight:500;line-height:1.6;margin-top:8px;padding:0 8px}
.btn{display:inline-block;background:var(--teal);color:#fff;font-weight:700;border-radius:10px;text-align:center}
.hero .btn{font-size:6.6px;width:71px;height:19px;line-height:19px;margin-top:10px}
.arrow{position:absolute;width:17px;height:17px;border-radius:50%;border:1px solid #fff;top:100px}

.section-title{width:480px;text-align:center;font-family:"Great Vibes",cursive;font-size:19px;color:var(--purple);font-weight:400}

.tile{position:absolute;overflow:hidden;color:#fff}
.tile-shade{position:absolute;inset:0;background:linear-gradient(180deg,rgba(0,0,0,0) 40%,rgba(0,0,0,0.28) 100%)}
.tile-info{position:absolute;top:68px}
.tile-name{font-size:11px;font-weight:600;line-height:1}
.tile-text{font-size:5.8px;margin-top:5px;white-space:nowrap}
.tile .btn{font-size:5.5px;height:15px;line-height:15px;padding:0 11px;margin-top:7px;border-radius:8px}

.shot{position:absolute;background:#fff;box-shadow:0 1px 3px rgba(0,0,0,0.14);width:120px}
.shot-img{display:block;width:120px}
.shot-cap{font-size:7px;text-align:center;color:#222;line-height:1}

.footer{left:0;width:480px;height:157px;background:var(--footer);color:#fff}
.f-head{position:absolute;top:35px;font-size:6.6px;font-weight:600}
.f-list{position:absolute;top:54px;list-style:none;font-size:5.2px}
.f-list li{height:10.7px}
.f-contact{position:absolute;left:45px;top:53px;font-size:5.4px;list-style:none}
.f-contact li{height:11.8px;display:flex;gap:5px;align-items:flex-start}
.f-contact svg{flex:none;margin-top:1px}
.f-email{position:absolute;left:329px;top:55px;width:107px;height:15px;border-radius:8px;background:#fff;font-size:5px;color:#777;padding-left:7px;line-height:15px}
.f-submit{position:absolute;left:329px;top:76px;width:62px;height:14px;line-height:14px;font-size:6px;border-radius:7px}
.f-social{position:absolute;left:337px;top:100px;display:flex;gap:3px}
.f-social span{display:block;width:14px;height:14px;border-radius:50%;background:#fff}
.f-rule{position:absolute;left:45px;top:129px;width:391px;height:1px;background:var(--rule)}
.f-copy{position:absolute;top:138px;width:480px;text-align:center;font-size:5.3px}
</style>
</head>
<body>
<div class="stage">

  <!-- Landing page -->
  <section class="page page--home">
    <div class="abs topbar">Lorem ipsum dolor sit amet, consectetur adipiscing elit,</div>
    <header class="abs header">
      <div class="abs brand"><span class="brand-dot"></span>Bram Kellet Photography</div>
      <div class="abs social"><span></span><span></span><span></span><span></span></div>
      <div class="abs call">Call Us: 123-456-789</div>
    </header>
    <nav class="abs nav">
      <a class="is-active">Home</a><a>About Me</a><a>Nature</a><a>Weddings</a><a>Potraits</a><a>Architecture</a><a>Shop</a><a>portfolio</a><a>News</a><a>Contact Us</a>
    </nav>
    <div class="abs hero" style="height:216px">
      <div class="photo" role="img" aria-label="Autumn trees beside a blue river" style="background:linear-gradient(112deg,#263016 0%,#4b5a22 16%,#8a7a2c 28%,#d08f2a 38%,#e0a83c 46%,#a8692a 54%,#35508c 64%,#27468a 80%,#1c3570 100%)"></div>
      <div class="arrow" style="left:13px"><svg width="15" height="15" viewBox="0 0 15 15"><path d="M8.5 4.5 5.5 7.5l3 3" fill="none" stroke="#fff" stroke-width="1.1"/></svg></div>
      <div class="arrow" style="left:449px"><svg width="15" height="15" viewBox="0 0 15 15"><path d="M6.5 4.5l3 3-3 3" fill="none" stroke="#fff" stroke-width="1.1"/></svg></div>
      <div class="hero-panel" style="top:58px;height:99px;padding-top:8px">
        <div class="hero-title">Bram Kellet Photography</div>
        <p class="hero-text">Lorem ipsum dolor sit amet, consectetur adipiscing elit, sed do eiusmod tempor incididunt</p>
        <span class="btn">GET STARTED</span>
      </div>
    </div>

    <h2 class="abs section-title" style="top:314px">Our Work</h2>

    <div class="tile" style="left:50px;top:355px;width:222px;height:130px">
      <div class="photo" role="img" aria-label="Dark ring resting on speckled stone" style="background:linear-gradient(125deg,#6f625a 0%,#a89588 30%,#8d7c70 48%,#2b3150 60%,#8a786c 74%,#5a4e4c 100%)"></div>
      <div class="tile-shade"></div>
      <div class="tile-info" style="left:20px"><div class="tile-name">Weddings</div><div class="tile-text">Lorem ipsum dolor sit amet, consectetur elit,</div><span class="btn">CONTACT ME</span></div>
    </div>
    <div class="tile" style="left:284px;top:355px;width:147px;height:130px">
      <div class="photo" role="img" aria-label="Red fox in a snowy forest" style="background:linear-gradient(135deg,#1f2a1c 0%,#3d4a2e 30%,#b8692c 48%,#d88a3e 56%,#3a3f36 70%,#c9ced4 100%)"></div>
      <div class="tile-shade"></div>
      <div class="tile-info" style="left:13px"><div class="tile-name">Nature</div><div class="tile-text">Lorem ipsum dolor sit amet, elit,</div><span class="btn">PURCHASE PRINTS</span></div>
    </div>
    <div class="tile" style="left:50px;top:495px;width:147px;height:130px">
      <div class="photo" role="img" aria-label="Black and white portrait study" style="background:linear-gradient(140deg,#cfcfcf 0%,#8a8a8a 30%,#3a3a3a 50%,#9c9c9c 70%,#1e1e1e 100%)"></div>
      <div class="tile-shade"></div>
      <div class="tile-info" style="left:13px"><div class="tile-name">Portraits</div><div class="tile-text">Lorem ipsum dolor sit amet, elit,</div><span class="btn">CONTACT ME</span></div>
    </div>
    <div class="tile" style="left:208px;top:495px;width:223px;height:130px">
      <div class="photo" role="img" aria-label="Brick and glass campus building" style="background:linear-gradient(180deg,#c5c9ce 0%,#b4b8bc 18%,#8f5e48 32%,#a06a50 55%,#4f3a34 78%,#5e6e48 100%)"></div>
      <div class="tile-shade"></div>
      <div class="tile-info" style="left:20px"><div class="tile-name">Architecture</div><div class="tile-text">Lorem ipsum dolor sit amet, consectetur elit,</div><span class="btn">CONTACT INFO</span></div>
    </div>

    <footer class="abs footer" style="top:666px">
      <div class="f-head" style="left:45px">CONTACT INFO</div>
      <ul class="f-contact">
        <li><svg width="6" height="6" viewBox="0 0 6 6"><path d="M1 1.2h4v1H4.4L4 3.8H2L1.6 2.2H1z M1.2 4.2h3.6V5H1.2z" fill="#fff"/></svg>(888) 888-8888</li>
        <li><svg width="6" height="6" viewBox="0 0 6 6"><rect x=".5" y="2" width="5" height="2.6" rx=".5" fill="#fff"/><rect x="1.5" y=".8" width="3" height="1.4" fill="#fff"/></svg>(888) 888-888</li>
        <li><svg width="6" height="6" viewBox="0 0 6 6"><rect x=".5" y="1.2" width="5" height="3.6" fill="#fff"/><path d="M.5 1.2 3 3.2l2.5-2" fill="none" stroke="#3f3571" stroke-width=".6"/></svg><u>info@bramkellet.example</u></li>
        <li><svg width="6" height="6" viewBox="0 0 6 6"><path d="M3 .4a1.8 1.8 0 0 1 1.8 1.8C4.8 3.5 3 5.6 3 5.6S1.2 3.5 1.2 2.2A1.8 1.8 0 0 1 3 .4z" fill="#fff"/></svg><span>#2868 Lorem ipsum dolor<br>sit amet, consectetur</span></li>
      </ul>
      <div class="f-head" style="left:149px">QUICK LINKS</div>
      <ul class="f-list" style="left:149px"><li>Home</li><li>About</li><li>Professional Gamer</li><li>Reviews</li><li>Gallery</li></ul>
      <div class="f-head" style="left:241px">INFORMATION</div>
      <ul class="f-list" style="left:241px"><li>Terms &amp; Conditions</li><li>Privacy Policy</li><li>Disclaimer</li><li>Site Map</li><li>Contact Us</li></ul>
      <div class="f-head" style="left:329px">NEWSLETTER SUBSCRIPTION</div>
      <div class="f-email">Enter your email</div>
      <div class="btn f-submit">SUBMIT</div>
      <div class="f-social"><span></span><span></span><span></span><span></span></div>
      <div class="f-rule"></div>
      <div class="f-copy">© Copyright 2020 Bram Kellet Photography, All Rights Reserved</div>
    </footer>
  </section>

  <!-- Weddings page -->
  <section class="page page--weddings">
    <div class="abs topbar">Lorem ipsum dolor sit amet, consectetur adipiscing elit,</div>
    <header class="abs header">
      <div class="abs brand"><span class="brand-dot"></span>Bram Kellet Photography</div>
      <div class="abs social"><span></span><span></span><span></span><span></span></div>
      <div class="abs call">Call Us: 123-456-789</div>
    </header>
    <nav class="abs nav">
      <a>Home</a><a>About Me</a><a>Nature</a><a class="is-active">Weddings</a><a>Potraits</a><a>Architecture</a><a>Shop</a><a>portfolio</a><a>News</a><a>Contact Us</a>
    </nav>
    <div class="abs hero" style="height:160px">
      <div class="photo" role="img" aria-label="Dark ring and gold band on speckled stone" style="background:linear-gradient(118deg,#7a6c62 0%,#b2a194 22%,#9a887b 38%,#2c3252 50%,#3a3f5e 58%,#a8977f 70%,#c2b3a4 85%,#8d7e72 100%)"></div>
      <div class="hero-panel" style="top:33px;height:93px;padding-top:6px">
        <div class="hero-title">Weddings</div>
        <p class="hero-text">Lorem ipsum dolor sit amet, consectetur adipiscing elit, sed do eiusmod tempor incididunt</p>
        <span class="btn" style="margin-top:7px">CONTACT ME</span>
      </div>
    </div>

    <h2 class="abs section-title" style="top:258px">Wedding Portfolio</h2>

    <figure class="shot" style="left:51px;top:293px;height:140px">
      <div class="shot-img" role="img" aria-label="Couple running on the beach" style="height:120px;background:linear-gradient(180deg,#e4dbcf 0%,#cfc2b2 35%,#7d7468 55%,#b9a58d 75%,#9c8468 100%)"></div>
      <figcaption class="shot-cap" style="margin-top:7px">Lorem ipsum dolor sit amet</figcaption>
    </figure>
    <figure class="shot" style="left:51px;top:443px;height:139px">
      <div class="shot-img" role="img" aria-label="Exchange of rings on green lawn" style="height:123px;background:linear-gradient(135deg,#f2f0ec 0%,#d8d5cf 30%,#e3bfa6 45%,#1e3826 60%,#28402c 75%,#263450 100%)"></div>
      <figcaption class="shot-cap" style="margin-top:2px">Lorem ipsum dolor sit amet</figcaption>
    </figure>
    <figure class="shot" style="left:51px;top:593px;height:150px">
      <div class="shot-img" role="img" aria-label="Proposal in a sunny meadow" style="height:129px;background:linear-gradient(180deg,#9fbf7a 0%,#4f7a34 35%,#d9c2a8 50%,#7a9a4a 70%,#9cb86a 100%)"></div>
      <figcaption class="shot-cap" style="margin-top:8px">Lorem ipsum dolor sit amet</figcaption>
    </figure>

    <figure class="shot" style="left:180px;top:293px;height:107px">
      <div class="shot-img" role="img" aria-label="Couple beside a decorated white car" style="height:87px;background:linear-gradient(180deg,#4f6e93 0%,#8fa3b8 25%,#e9ecee 50%,#f1d5dc 65%,#f7f6f5 100%)"></div>
      <figcaption class="shot-cap" style="margin-top:6px">Lorem ipsum dolor sit amet</figcaption>
    </figure>
    <figure class="shot" style="left:180px;top:410px;height:150px">
      <div class="shot-img" role="img" aria-label="Guests cheering the newlyweds" style="height:130px;background:linear-gradient(180deg,#d7d4cf 0%,#6f7070 30%,#efe9e2 55%,#d99a9a 68%,#6e9a44 85%,#5a8236 100%)"></div>
      <figcaption class="shot-cap" style="margin-top:7px">Lorem ipsum dolor sit amet</figcaption>
    </figure>
    <figure class="shot" style="left:180px;top:573px;height:138px">
      <div class="shot-img" role="img" aria-label="Beach ceremony arch with white drapes" style="height:121px;background:linear-gradient(180deg,#8cbde6 0%,#5f98c8 30%,#2d6a9c 45%,#f2f1ee 60%,#e2ddd6 80%,#b9afa2 100%)"></div>
      <figcaption class="shot-cap" style="margin-top:7px">Lorem ipsum dolor sit amet</figcaption>
    </figure>

    <figure class="shot" style="left:309px;top:293px;height:172px">
      <div class="shot-img" role="img" aria-label="Couple on the beach at sunset" style="height:153px;background:linear-gradient(180deg,#f6c178 0%,#f0a152 30%,#e8c6b4 50%,#e38f45 70%,#a86a44 90%,#7c5038 100%)"></div>
      <figcaption class="shot-cap" style="margin-top:6px">Lorem ipsum dolor sit amet</figcaption>
    </figure>
    <figure class="shot" style="left:309px;top:475px;height:106px">
      <div class="shot-img" role="img" aria-label="Hands with wedding rings" style="height:87px;background:linear-gradient(135deg,#2a3a2c 0%,#6f7f6a 25%,#ead0bc 45%,#f5f4f2 62%,#dcdde0 78%,#1b2130 100%)"></div>
      <figcaption class="shot-cap" style="margin-top:6px">Lorem ipsum dolor sit amet</figcaption>
    </figure>
    <figure class="shot" style="left:309px;top:592px;height:151px">
      <div class="shot-img" role="img" aria-label="Hands placing a wedding ring" style="height:130px;background:linear-gradient(135deg,#34463a 0%,#7a8a76 25%,#ecd3bf 45%,#f6f5f3 62%,#dfe0e3 78%,#1b2130 100%)"></div>
      <figcaption class="shot-cap" style="margin-top:7px">Lorem ipsum dolor sit amet</figcaption>
    </figure>

    <footer class="abs footer" style="top:783px">
      <div class="f-head" style="left:45px">CONTACT INFO</div>
      <ul class="f-contact">
        <li><svg width="6" height="6" viewBox="0 0 6 6"><path d="M1 1.2h4v1H4.4L4 3.8H2L1.6 2.2H1z M1.2 4.2h3.6V5H1.2z" fill="#fff"/></svg>(888) 888-8888</li>
        <li><svg width="6" height="6" viewBox="0 0 6 6"><rect x=".5" y="2" width="5" height="2.6" rx=".5" fill="#fff"/><rect x="1.5" y=".8" width="3" height="1.4" fill="#fff"/></svg>(888) 888-888</li>
        <li><svg width="6" height="6" viewBox="0 0 6 6"><rect x=".5" y="1.2" width="5" height="3.6" fill="#fff"/><path d="M.5 1.2 3 3.2l2.5-2" fill="none" stroke="#3f3571" stroke-width=".6"/></svg><u>info@bramkellet.example</u></li>
        <li><svg width="6" height="6" viewBox="0 0 6 6"><path d="M3 .4a1.8 1.8 0 0 1 1.8 1.8C4.8 3.5 3 5.6 3 5.6S1.2 3.5 1.2 2.2A1.8 1.8 0 0 1 3 .4z" fill="#fff"/></svg><span>#2868 Lorem ipsum dolor<br>sit amet, consectetur</span></li>
      </ul>
      <div class="f-head" style="left:149px">QUICK LINKS</div>
      <ul class="f-list" style="left:149px"><li>Home</li><li>About</li><li>Professional Gamer</li><li>Reviews</li><li>Gallery</li></ul>
      <div class="f-head" style="left:241px">INFORMATION</div>
      <ul class="f-list" style="left:241px"><li>Terms &amp; Conditions</li><li>Privacy Policy</li><li>Disclaimer</li><li>Site Map</li><li>Contact Us</li></ul>
      <div class="f-head" style="left:329px">NEWSLETTER SUBSCRIPTION</div>
      <div class="f-email">Enter your email</div>
      <div class="btn f-submit">SUBMIT</div>
      <div class="f-social"><span></span><span></span><span></span><span></span></div>
      <div class="f-rule"></div>
      <div class="f-copy">© Copyright 2020 Bram Kellet Photography, All Rights Reserved</div>
    </footer>
  </section>

</div>
</body>
</html>
```